Design Startseite Kanzlei-Homepage
Zielgruppe
Wir sind eine Rechtsanwaltskanzlei in Kempten (Allgäu) und regional sowie überregional in verschiedenen Rechtsgebieten tätig. Unsere Zielgruppe sind sowohl private als auch gewerbliche Mandanten.
Aufgabenstellung
Die bestehende Gestaltung wirkt derzeit aus unserer Sicht überholt. Insbesondere soll das bislang dominierende Rot vollständig entfallen.
Stattdessen stellen wir uns ein modernes, hochwertiges Erscheinungsbild vor, primär in dunklen Farbtönen (Anthrazit/Schwarz) kombiniert mit Beige- bzw. warmen Naturtönen. Ziel ist eine klare visuelle Anlehnung an unsere Kanzleiräumlichkeiten (siehe Fotos).
Die Webseite soll insgesamt moderner, klarer und visuell anspruchsvoller wirken, ohne an Seriosität und Zugänglichkeit einzubüßen. Die Balance zwischen hochwertigem Erscheinungsbild und mandantenorientierter Nutzerführung steht für uns im Vordergrund.

```html
<!DOCTYPE html>
<html lang="de">
<head>
<meta charset="utf-8">
<title>Kanzlei am Lindenhof – Redesign</title>
<link href="https://fonts.googleapis.com/css2?family=Source+Serif+4:wght@400;500&family=Inter:wght@400;500;600;700&display=swap" rel="stylesheet">
<style>
:root{
  --ink:#121211;--charcoal:#1c1d1b;--graphite:#2b2c29;--stone:#e4ded4;--sand:#cbb99f;
  --oak:#a77f55;--cream:#f4efe7;--paper:#fbf8f2;--greige:#bbb8b2;--text:#2a2a28;--muted:#6a6863;
  --serif:"Source Serif 4",Georgia,serif;--sans:"Inter",Arial,sans-serif;
}
*{margin:0;padding:0;box-sizing:border-box}
html,body{width:1200px;height:2233px;overflow:hidden;background:#fff;font-family:var(--sans);color:var(--text)}
.abs{position:absolute}
.board-label{left:22px;top:22px;font-size:8px;font-weight:600;letter-spacing:.06em;color:var(--oak)}
.board-title{left:22px;top:42px;font-family:var(--serif);font-size:32px;color:var(--text)}
.page{left:22px;top:118px;width:568px;height:2115px;overflow:hidden}
.sec{position:absolute;left:0;width:568px}
.eyebrow{font-size:4.5px;font-weight:700;letter-spacing:.08em;text-transform:uppercase;color:var(--oak)}
.h-serif{font-family:var(--serif);font-weight:400;line-height:1.15}
.small{font-size:5px;line-height:1.7}
.btn{display:inline-block;font-size:4.5px;font-weight:600;padding:4px 8px;border:1px solid var(--sand)}
.btn-fill{background:var(--sand);color:var(--ink)}
.btn-line{color:#fff}
/* hero */
.hero{top:0;height:405px;background:linear-gradient(100deg,#141413 0%,#2c2620 45%,#5a4a38 70%,#2a2724 100%)}
.nav{position:absolute;left:0;top:0;width:568px;height:28px;background:rgba(18,18,17,.85)}
.logo{position:absolute;left:108px;top:10px;font-size:10px;font-weight:600;color:#fff;letter-spacing:.02em}
.nav-links{position:absolute;left:356px;top:12px;font-size:4.5px;color:#ddd;display:flex;gap:11px}
.nav-phone{position:absolute;left:510px;top:6px;border:1px solid #aaa;color:#fff;font-size:5px;padding:4px 5px}
.hero-copy{position:absolute;left:107px;top:85px;width:280px;color:#fff}
.hero-copy h1{font-size:29px;line-height:30px;margin:6px 0 14px}
.hero-copy p{color:#ddd;width:200px}
.stats{position:absolute;left:107px;top:306px;width:292px;height:38px;border:1px solid #666;display:flex;background:rgba(18,18,17,.5)}
.stats div{flex:1;border-right:1px solid #666;color:#fff;text-align:center;padding-top:7px;font-size:4.2px;line-height:1.5}
.stats div:last-child{border:none}
.stats b{display:block;font-size:7px}
/* intro */
.intro{top:405px;height:178px;background:var(--paper)}
.kcard{position:absolute;left:386px;top:50px;width:128px;height:79px;background:var(--ink);color:#fff;padding:12px 11px;box-shadow:0 8px 20px rgba(0,0,0,.15)}
/* areas */
.areas{top:583px;height:297px;background:var(--ink);color:#fff}
.grid{position:absolute;left:106px;top:104px;width:372px;height:158px;border:1px solid #444;display:grid;grid-template-columns:repeat(3,1fr);grid-template-rows:1fr 1fr}
.cell{border-right:1px solid #444;border-bottom:1px solid #444;padding:9px 17px;position:relative}
.cell:nth-child(3n){border-right:none}.cell:nth-child(n+4){border-bottom:none}
.cell .num{font-size:4px;color:#bbb}
.cell .ic{position:absolute;right:12px;top:8px;width:12px;height:12px;border:1px solid var(--sand);border-radius:50%}
.cell h3{font-family:var(--serif);font-weight:400;font-size:9px;margin:14px 0 5px}
.cell p{font-size:4.2px;line-height:1.6;color:#bbb}
/* video */
.video{top:880px;height:186px;background:var(--graphite);color:#fff}
.ph{position:absolute}
/* reviews */
.reviews{top:1066px;height:193px;background:var(--cream)}
.rcard{position:absolute;top:76px;width:135px;height:78px;background:var(--paper);padding:8px 11px}
.stars{font-size:5px;color:var(--oak);letter-spacing:1px}
.rcard p{font-family:var(--serif);font-size:5.5px;line-height:1.4;margin:5px 0 7px}
.rcard span{font-size:3.8px;color:#aaa}
/* rooms + team */
.rooms{top:1259px;height:561px;background:var(--paper)}
/* contact */
.contact{top:1820px;height:295px;background:var(--ink)}
.cpanel{position:absolute;left:94px;top:38px;width:153px;height:204px;background:var(--graphite);color:#fff;padding:17px 12px}
.cpanel dl{font-size:4.2px;line-height:1.6;margin-top:12px}
.cpanel dt{font-weight:700;margin-top:5px}
/* right column */
.right{left:608px;width:574px}
.r-h{font-family:var(--serif);font-weight:400;font-size:21px;color:var(--text)}
.r-sub{font-size:11px;font-weight:600;color:var(--oak)}
.r-p{font-size:11px;line-height:20px;color:#333}
.sw{position:absolute;width:62px;height:38px}
.swl{position:absolute;font-size:7.5px;line-height:1.3;color:#333;width:66px}
.quote{font-family:var(--serif);font-size:17.5px;line-height:28px;letter-spacing:-.01em;color:var(--sand)}
.thumb{position:absolute;top:492px;width:280px;height:197px;overflow:hidden;color:#fff}
.thumb h4{position:absolute;left:40px;top:52px;font-family:var(--serif);font-weight:400;font-size:14px;line-height:14px}
.thumb .tnav{position:absolute;left:0;top:0;width:100%;height:10px;background:rgba(18,18,17,.7);font-size:3.5px;padding:3px 9px}
.thumb .tstats{position:absolute;left:40px;top:170px;width:199px;height:20px;border:1px solid #555}
/* mobile */
.mobile{position:absolute;left:692px;top:1124px;width:340px;height:767px;overflow:hidden;border-radius:18px;background:var(--paper)}
.m-hero{position:absolute;left:0;top:0;width:340px;height:578px;background:linear-gradient(180deg,#1c1d1b 0%,#3a3630 40%,#4a4032 60%,#1c1d1b 100%)}
.m-stats{position:absolute;left:23px;top:353px;width:292px;height:166px;border:1px solid #555;background:rgba(28,29,27,.6);color:#fff}
.m-stats div{height:55px;border-bottom:1px solid #555;padding:14px 12px;font-size:7px;color:#ccc}
.m-stats div:last-child{border:none}
.m-stats b{display:block;font-size:10px;color:#fff;margin-bottom:5px}
</style>
</head>
<body>
<div class="abs board-label">PRESENTATION</div>
<div class="abs board-title">Kanzlei am Lindenhof - Redesign</div>

<main class="abs page">
  <section class="sec hero">
    <div class="ph" role="img" aria-label="Foto: Empfangsbereich der Kanzlei mit Holzverkleidung und Tresen" style="inset:0;background:linear-gradient(100deg,rgba(18,18,17,.85) 0%,rgba(30,27,24,.55) 45%,rgba(90,74,56,.3) 70%,rgba(20,20,19,.5) 100%)"></div>
    <nav class="nav">
      <div class="logo">KANZLEI AM LINDENHOF</div>
      <div class="nav-links"><span>Rechtsgebiete</span><span>Kanzlei</span><span>WissenKompakt</span><span>Kontakt</span></div>
      <div class="nav-phone">0831 - 470 219 00</div>
    </nav>
    <div class="hero-copy">
      <div class="eyebrow" style="color:var(--sand)">Rechtsanwälte und Fachanwälte in Kempten</div>
      <h1 class="h-serif">Klarer<br>Rechtsbeistand<br>für Entscheidungen,<br>die Gewicht haben.</h1>
      <p class="small">Die Kanzlei am Lindenhof verbindet spezialisierte Beratung mit persönlicher Erreichbarkeit. Für private und gewerbliche Mandanten in Kempten, im Allgäu und darüber hinaus.</p>
      <div style="margin-top:12px"><span class="btn btn-fill">Termin vereinbaren</span> &nbsp;<span class="btn btn-line">Rechtsgebiete finden</span></div>
    </div>
    <div class="stats">
      <div><b>7</b>Rechtsanwälte mit unterschiedlichen<br>Fachrichtungen</div>
      <div><b>Kempten</b>Zentral am Lindenhof,<br>Lindenstr. 4</div>
      <div><b>Privat &amp; Gewerbe</b>Beratung für Menschen<br>und Unternehmen</div>
    </div>
  </section>

  <section class="sec intro">
    <div class="abs" style="left:58px;top:38px;width:260px">
      <div class="eyebrow">Mandantenorientiert beraten</div>
      <h2 class="h-serif" style="font-size:15px;margin:6px 0 8px;white-space:nowrap">Breit aufgestellt, persönlich geführt</h2>
      <p class="small">Unser Anwaltsteam ist in unterschiedlichen Fachrichtungen spezialisiert. So erhalten Mandanten rechtliche Unterstützung, die zum konkreten Anliegen passt: fachlich fundiert, klar in der Einschätzung und verlässlich in der Begleitung.</p>
      <p class="small" style="margin-top:6px">Durch die thematische Vielfalt der Kanzlei können viele Anliegen direkt im Haus bearbeitet werden. Das spart Abstimmungswege und schafft eine Beratung, die individuelle Interessen ebenso berücksichtigt wie aktuelle Rechtsprechung und Praxis.</p>
    </div>
    <div class="kcard">
      <h3 class="h-serif" style="font-size:10px;margin-bottom:6px">Unsere Kanzlei</h3>
      <p style="font-size:4.6px;line-height:1.5">Lernen Sie unsere Kanzlei persönlich kennen und erfahren Sie, wie wir arbeiten. Mit klarer Expertise für Ihr Anliegen.</p>
      <div style="margin-top:8px"><span class="btn btn-fill">Kanzlei kennenlernen</span></div>
    </div>
  </section>

  <section class="sec areas">
    <div class="abs" style="left:115px;top:42px">
      <div class="eyebrow" style="color:#ddd">Ausgewählte Rechtsgebiete</div>
      <h2 class="h-serif" style="font-size:16px;margin-top:6px">Kompetenz dort, wo<br>Ihr Anliegen beginnt.</h2>
    </div>
    <div class="grid">
      <div class="cell"><span class="num">01</span><i class="ic"></i><h3>Familienrecht</h3><p>Beratung bei Scheidung, Unterhalt, Umgangs- und Sorgerecht mit Blick auf tragfähige Lösungen.</p></div>
      <div class="cell"><span class="num">02</span><i class="ic"></i><h3>Arbeitsrecht</h3><p>Unterstützung für Arbeitnehmer und Arbeitgeber bei Kündigung, Aufhebungsvertrag und Zeugnisfragen.</p></div>
      <div class="cell"><span class="num">03</span><i class="ic"></i><h3>Verkehrsrecht</h3><p>Vertretung nach Unfällen, Bußgeldverfahren, Fahrerlaubnisfragen und Schadensregulierung.</p></div>
      <div class="cell"><span class="num">04</span><i class="ic"></i><h3>Familienrecht</h3><p>Kurzfristiger Rechtsbeistand bei Ermittlungen, Durchsuchungen, Vernehmungen und Gerichtsverfahren.</p></div>
      <div class="cell"><span class="num">05</span><i class="ic"></i><h3>Erbrecht</h3><p>Rechtliche Begleitung für Erben, Erblasser und Familien bei komplexen Nachlassfragen.</p></div>
      <div class="cell"><span class="num">06</span><i class="ic"></i><h3>Mietrecht</h3><p>Beratung für Vermieter, Mieter und Wohnungseigentümer in Kempten und im Allgäu.</p></div>
    </div>
  </section>

  <section class="sec video">
    <div class="ph" role="img" aria-label="Foto: drei Anwälte im Gespräch am Besprechungstisch" style="left:0;top:0;width:292px;height:186px;background:linear-gradient(135deg,#d9d6cf,#eceae4 50%,#8a8f86)"></div>
    <svg class="abs" style="left:322px;top:30px" width="28" height="28" viewBox="0 0 28 28"><circle cx="14" cy="14" r="14" fill="#e4ded4"/><path d="M11 9 L19 14 L11 19Z" fill="#121211"/></svg>
    <div class="abs" style="left:322px;top:68px;width:232px">
      <div class="eyebrow" style="color:var(--sand)">Image-Video</div>
      <h2 class="h-serif" style="font-size:16px;margin:4px 0 6px">Einblicke in Arbeitsweise,<br>Räume und Team.</h2>
      <p style="font-size:4.3px;line-height:1.6;color:#ddd">Das Video-Modul kann prominent zeigen, was Mandanten vor Ort erwartet: eine moderne Kanzlei, klare Abläufe und Ansprechpartner, die erreichbar bleiben.</p>
      <div style="margin-top:7px"><span class="btn btn-fill">Video ansehen</span> <span class="btn btn-line">Erstgespräch vereinbaren</span></div>
    </div>
  </section>

  <section class="sec reviews">
    <div class="abs" style="left:80px;top:41px">
      <div class="eyebrow">Mandantenbewertungen</div>
      <h2 class="h-serif" style="font-size:16px;margin-top:5px">Vertrauen sichtbar machen.</h2>
    </div>
    <div class="rcard" style="left:80px"><div class="stars">★★★★★</div><p>Sehr gute Betreuung, professionelle Bearbeitung und ein verlässlicher Partner für Rechtsfragen.</p><span>Mandantenstimme, Unternehmen</span></div>
    <div class="rcard" style="left:222px"><div class="stars">★★★★★</div><p>Ausführliche Beratung, schnelle Terminvergabe und zielstrebige Vertretung der Interessen.</p><span>Mandantenstimme, Familienrecht</span></div>
    <div class="rcard" style="left:364px"><div class="stars">★★★★★</div><p>Unkomplizierte Kommunikation, verständliche Einschätzung und eine Lösung ohne unnötige Umstände.</p><span>Mandantenstimme, Verkehrsrecht</span></div>
  </section>

  <section class="sec rooms">
    <div class="abs" style="left:106px;top:42px">
      <div class="eyebrow">Räumlichkeiten</div>
      <h2 class="h-serif" style="font-size:16px;margin-top:5px">Hochwertig, ruhig, nahbar.</h2>
    </div>
    <div class="ph" role="img" aria-label="Foto: Empfangstresen mit Holzwand und Lichtleiste" style="left:106px;top:79px;width:209px;height:259px;background:linear-gradient(180deg,#d8d4cc,#b08a5e 55%,#4a4a48)"></div>
    <div class="ph" role="img" aria-label="Foto: Wartebereich mit Sitzbank und Wandbild" style="left:336px;top:79px;width:142px;height:89px;background:linear-gradient(180deg,#e8e4dc,#8a7356 60%,#3a3a38)"></div>
    <div class="ph" role="img" aria-label="Foto: Flur mit Holzverkleidung" style="left:336px;top:182px;width:142px;height:156px;background:linear-gradient(90deg,#b89064,#e6e2da 40%,#5a5a58 70%,#c29a6c)"></div>
    <div class="abs" style="left:106px;top:388px;width:132px">
      <div class="eyebrow" style="color:var(--text)">Team</div>
      <h2 class="h-serif" style="font-size:15px;line-height:17px;margin:5px 0 9px">Viele Fachrichtungen, ein gemeinsamer Anspruch.</h2>
      <p style="font-size:4.5px;line-height:1.6;color:#444">Die Teamvorstellung sollte auf der Startseite nicht alles erklären, sondern Vertrauen aufbauen und den Weg zu den einzelnen Anwälten öffnen.</p>
      <div style="margin-top:6px"><span class="btn btn-fill">Anwälte ansehen</span></div>
    </div>
    <div class="ph" role="img" aria-label="Foto: Gruppenbild des Kanzleiteams auf einem Platz" style="left:268px;top:388px;width:210px;height:131px;background:linear-gradient(180deg,#cfcdc8,#4a4a4c 50%,#c9c7c2)"></div>
  </section>

  <section class="sec contact">
    <div class="cpanel">
      <div class="eyebrow" style="color:var(--sand)">Kontakt und Anfahrt</div>
      <h2 class="h-serif" style="font-size:16px;margin-top:5px">Ihr erster<br>Schritt zur<br>rechtlichen<br>Klärung.</h2>
      <dl>
        <dt>Kanzlei am Lindenhof</dt><dd>Lindenstraße 4, 87435 Kempten</dd>
        <dt>Telefon</dt><dd>0831 - 470 219 00</dd>
        <dt>E-Mail</dt><dd>info@kanzlei-lindenhof.de</dd>
      </dl>
      <div style="margin-top:10px"><span class="btn btn-fill">Jetzt anrufen</span> <span class="btn btn-line">Nachricht senden</span></div>
    </div>
    <div class="ph" role="img" aria-label="Stadtplan mit Standort der Kanzlei in Kempten" style="left:247px;top:38px;width:229px;height:204px;background:#ecebe8"></div>
  </section>
</main>

<h2 class="abs right r-h" style="top:114px">Die neue Website übersetzt die Kanzleiräume ins Digitale.</h2>
<div class="abs right r-sub" style="top:163px">Die Farben</div>
<p class="abs right r-p" style="top:181px">Die Farben sind direkt aus Empfang, Holzflächen, Teppich und Beleuchtung abgeleitet. So wirkt die Website wie eine digitale Fortsetzung der Kanzlei.</p>

<div class="sw" style="left:608px;top:222px;background:var(--ink)"></div><div class="swl" style="left:608px;top:271px">Ink - #121211</div>
<div class="sw" style="left:684px;top:222px;background:var(--charcoal)"></div><div class="swl" style="left:684px;top:271px">Charcoal -<br>#1c1d1b</div>
<div class="sw" style="left:759px;top:222px;background:var(--graphite)"></div><div class="swl" style="left:759px;top:271px">Graphite -<br>#2b2c29</div>
<div class="sw" style="left:835px;top:222px;background:var(--stone)"></div><div class="swl" style="left:835px;top:271px">Stone - #e4ded4</div>
<div class="sw" style="left:911px;top:222px;background:var(--sand)"></div><div class="swl" style="left:911px;top:271px">Sand - #cbb99f</div>
<div class="sw" style="left:608px;top:302px;background:var(--oak)"></div><div class="swl" style="left:608px;top:352px">Oak - #a77f55</div>
<div class="sw" style="left:684px;top:302px;background:var(--cream)"></div><div class="swl" style="left:684px;top:352px">Cream - #f4efe7</div>
<div class="sw" style="left:759px;top:302px;background:var(--paper)"></div><div class="swl" style="left:759px;top:352px">Paper - #fbf8f2</div>
<div class="sw" style="left:835px;top:302px;background:var(--greige)"></div><div class="swl" style="left:835px;top:352px">Greige -<br>#bbb8b2</div>

<div class="abs right r-sub" style="top:400px">Der Hero-Bereich</div>
<p class="abs right r-p" style="top:418px">Wechsel zwischen Innenaufnahme und Außenaufnahme.<br>zentrale Aussage: „Klarer Rechtsbeistand, für Entscheidungen, die Gewicht haben.“<br>direkte CTAs: Termin vereinbaren, Rechtsgebiet finden</p>

<div class="thumb" style="left:608px;background:linear-gradient(100deg,#141413,#3a3028 50%,#6a5540 70%,#2a2724)" role="img" aria-label="Hero-Variante mit Innenaufnahme des Empfangs">
  <div class="tnav">KANZLEI AM LINDENHOF</div>
  <h4>Klarer<br>Rechtsbeistand,<br>wenn<br>Entscheidungen<br>Gewicht haben.</h4>
  <div class="tstats"></div>
</div>
<div class="thumb" style="left:903px;background:linear-gradient(180deg,#2a2b2c,#5a5040 55%,#1c1d1b)" role="img" aria-label="Hero-Variante mit Außenaufnahme des Kanzleigebäudes">
  <div class="tnav">KANZLEI AM LINDENHOF</div>
  <h4>Klarer<br>Rechtsbeistand,<br>wenn<br>Entscheidungen<br>Gewicht haben.</h4>
  <div class="tstats"></div>
</div>

<p class="abs right r-p" style="top:740px">Die Screens sind in Skizzbrett erstellt und liegen auch als Html/CSS vor Für die produktive Website wäre eine Umsetzung mit Nodeframe/Windstyle und optional schlankem (eigenem) CMS möglich, damit Inhalte später selbst gepflegt werden können.</p>
<p class="abs right quote" style="top:822px">Der neue Auftritt soll nicht lauter wirken, sondern klarer: moderner, hochwertiger und näher an der tatsächlichen Atmosphäre der Kanzlei.</p>
<div class="abs right r-sub" style="top:905px">Mobile Ansicht</div>
<p class="abs right r-p" style="top:923px">Die mobile Version ist bewusst reduziert und klar aufgebaut. Die großen Bildflächen und die hochwertige Farbwelt bleiben erhalten, aber die Inhalte werden untereinander gestapelt, damit Mandanten schnell lesen und handeln können.</p>
<p class="abs right r-p" style="top:1003px">Da viele Mandanten die Seite zuerst mobil aufrufen, ist die mobile Version nicht nur eine verkleinerte Desktopseite, sondern eine klare, lineare Beratungsstrecke bis zur Kontaktaufnahme.</p>

<div class="mobile">
  <div class="m-hero" role="img" aria-label="Außenaufnahme des Kanzleigebäudes in der Abenddämmerung"></div>
  <div class="abs" style="left:12px;top:16px;font-size:11px;font-weight:600;color:#fff">KANZLEI AM LINDENHOF</div>
  <div class="abs" style="left:238px;top:12px;border:1px solid #888;color:#fff;font-size:7.5px;font-weight:600;padding:5px 8px">0831 - 470 219 00</div>
  <div class="abs" style="left:23px;top:122px;width:300px;color:#fff">
    <div class="eyebrow" style="font-size:7px;color:#ddd">Rechtsanwälte und Fachanwälte in Kempten</div>
    <h1 class="h-serif" style="font-size:24px;line-height:24px;margin:12px 0 12px">Klarer Rechtsbeistand, wenn Entscheidungen Gewicht haben.</h1>
    <p style="font-size:8.5px;line-height:1.6;color:#eee">Die Kanzlei am Lindenhof verbindet spezialisierte Beratung mit persönlicher Erreichbarkeit. Für private und gewerbliche Mandanten in Kempten, im Allgäu und darüber hinaus.</p>
    <div style="margin-top:14px;display:flex;gap:4px"><span class="btn btn-fill" style="font-size:8px;padding:8px 13px">Termin vereinbaren</span><span class="btn btn-line" style="font-size:8px;padding:8px 13px">Rechtsgebiet finden</span></div>
  </div>
  <div class="m-stats">
    <div><b>7</b>Rechtsanwälte mit unterschiedlichen Fachrichtungen</div>
    <div><b>Kempten</b>Zentral am Lindenhof, Lindenstraße 4</div>
    <div><b>Privat &amp; Gewerbe</b>Beratung für Menschen und Unternehmen</div>
  </div>
  <div class="abs" style="left:13px;top:605px;width:312px">
    <div class="eyebrow" style="font-size:6.5px">Mandantenorientiert beraten</div>
    <h2 class="h-serif" style="font-size:17px;margin:8px 0 10px;white-space:nowrap">Breit aufgestellt, persönlich geführt.</h2>
    <p style="font-size:8.5px;line-height:1.8;color:#555">Unser Anwaltsteam ist in unterschiedlichen Fachrichtungen spezialisiert. So erhalten Mandanten rechtliche Unterstützung, die zum konkreten Anliegen passt: fachlich fundiert, klar in der Einschätzung und verlässlich in der Begleitung.</p>
    <p style="font-size:8.5px;line-height:1.8;color:#555;margin-top:8px">Durch die thematische Vielfalt der Kanzlei können viele Anliegen direkt im Haus bearbeitet werden.</p>
  </div>
</div>
</body>
</html>
```